Tidewell Climate Business Card Design

Design new, 2 sides, business cards for a residential and light commercial heating, air conditioning contractor.

Target Market(s)

Homeowners, small businesses

Industry/Entity Type

Business

Contact Information for Business Card

Dominic Westerhall
Phone - 862-415-2736
Email
Address - PO box 518
Brightwater NJ 07912
Website - www.HarborBreezeLLC.example

Requirements
Must have
• logo, company colors, standard size with no die cut, so I can use nova stamp

```html
<!DOCTYPE html>
<html lang="en">
<head>
<meta charset="utf-8">
<title>Tidewell Climate Business Card</title>
<link rel="stylesheet" href="https://fonts.googleapis.com/css2?family=PT+Sans:ital,wght@0,400;0,700;1,400&display=swap">
<style>
  :root {
    --brand-red: #9b1f32;
    --brand-orange: #f08a24;
    --ink: #444444;
    --paper: #ffffff;
    --cream: #fbeecb;
    --backdrop: #e4e1dd;
  }
  * { box-sizing: border-box; margin: 0; padding: 0; }
  html, body {
    width: 1200px; height: 987px; overflow: hidden;
    background: var(--backdrop);
    font-family: "PT Sans", Arial, sans-serif;
  }
  .canvas { position: relative; width: 1200px; height: 987px; }
  .card {
    position: absolute; left: 293px; width: 615px; height: 351px;
    box-shadow: 0 2px 6px rgba(0,0,0,0.25);
  }
  .card-front { top: 130px; background: var(--paper); }
  .card-back { top: 506px; background: var(--brand-red); }

  .accent-bar {
    position: absolute; left: 0; top: 74px; width: 12px; height: 46px;
    background: var(--brand-red);
  }
  .contact { position: absolute; left: 40px; top: 74px; color: var(--ink); }
  .contact-name {
    font-size: 23px; font-weight: 700; color: var(--brand-red);
    letter-spacing: 0.3px; line-height: 28px;
  }
  .contact-title { font-size: 18px; color: var(--brand-orange); line-height: 22px; }
  .contact-address { margin-top: 10px; font-size: 16.5px; line-height: 23px; }
  .contact-list { list-style: none; margin-top: 6px; }
  .contact-list li {
    display: flex; align-items: center; gap: 9px;
    font-size: 16px; line-height: 23.5px;
  }
  .contact-list svg { width: 15px; height: 15px; flex: none; fill: var(--brand-red); }

  .brand-name {
    position: absolute; font-weight: 700; text-align: center;
    transform: translate(-50%, -50%); letter-spacing: 0.5px;
    line-height: 1.05; white-space: nowrap;
  }
  .card-front .brand-name { left: 451px; top: 186px; color: var(--brand-red); font-size: 40px; }
  .card-back .brand-name { left: 307px; top: 171px; color: var(--cream); font-size: 46px; }

  .tagline {
    position: absolute; left: 0; right: 0; top: 278px;
    text-align: center; color: var(--paper);
    font-style: italic; font-size: 17px; line-height: 21px;
  }
</style>
</head>
<body>
<main class="canvas">
  <section class="card card-front" aria-label="Card front">
    <div class="accent-bar"></div>
    <div class="contact">
      <h1 class="contact-name">DOMINIC WESTERHALL</h1>
      <p class="contact-title">CEO/Founder</p>
      <p class="contact-address">PO box 518<br>Brightwater NJ 07912</p>
      <ul class="contact-list">
        <li><svg viewBox="0 0 16 16"><path d="M3.5 1.5l2.5 0 1.2 3.3-1.6 1.2a8 8 0 0 0 4.4 4.4l1.2-1.6 3.3 1.2 0 2.5c0 .8-.7 1.5-1.5 1.5A12 12 0 0 1 2 3c0-.8.7-1.5 1.5-1.5z"/></svg>862 415 2736</li>
        <li><svg viewBox="0 0 16 16"><path d="M4.5 0h7a1 1 0 0 1 1 1v14a1 1 0 0 1-1 1h-7a1 1 0 0 1-1-1V1a1 1 0 0 1 1-1zM5 2v10h6V2zm3 11a1 1 0 1 0 0 2 1 1 0 0 0 0-2z"/></svg>862 415 2791</li>
        <li><svg viewBox="0 0 16 16"><path d="M4 1h8v4H4zM1 6h14v6h-2v3H3v-3H1zM4.5 10v3.5h7V10z"/></svg>862 415 2740</li>
        <li><svg viewBox="0 0 16 16"><path d="M1 3h14v10H1zM2.2 4.2L8 8.6l5.8-4.4z"/></svg>dominic@tidewellclimate.example</li>
        <li><svg viewBox="0 0 16 16"><path d="M8 1a7 7 0 1 0 0 14A7 7 0 0 0 8 1zm0 1.5c.9 0 1.9 1.9 2.2 4.5H5.8C6.1 4.4 7.1 2.5 8 2.5zM5.8 9h4.4c-.3 2.6-1.3 4.5-2.2 4.5S6.1 11.6 5.8 9z"/></svg>www.TidewellClimateLLC.example</li>
      </ul>
    </div>
    <p class="brand-name">Tidewell<br>Climate</p>
  </section>

  <section class="card card-back" aria-label="Card back">
    <p class="brand-name">Tidewell<br>Climate</p>
    <p class="tagline">Residential &amp; light commercial heating<br>Air conditioning contractor</p>
  </section>
</main>
</body>
</html>
```